Business card for Luxury Portable Restroom Trailer company

We are a Luxury Portable Restroom Trailer Company Called FALCRIDGE HIRES. Based in Orange County California. We provide portable restroom trailers for events, such as, Weddings, Concerts, Charity events, Sporting events, Tournaments, Corporate events, ect. We rent and Sell the Luxury restrooms. Our colors are white, grey, and Orange. As you will see in the logo we uploaded.
There are 2 people in the company so the names and titles will change for the 3 people but card will remain the same. Here is the information for each Person: Dwight Penner CFO 555 318-0476
next Person: Leon Marchetti VP 555 318-0476
Next Person: Owen Marchetti CEO 555 318-0476
Information to include on the card: Luxury Restroom Trailers Rental and Sales. Weddings, Concerts, Charity, Sporting and Corp. Events.

```html
<!DOCTYPE html>
<html lang="en">
<head>
<meta charset="UTF-8">
<title>Falcridge Hires – Business Card</title>
<link rel="stylesheet" href="https://fonts.googleapis.com/css2?family=Montserrat:wght@300;400;600;700;800&display=swap">
<style>
  :root {
    --orange: #e2621f;
    --orange-deep: #d4541a;
    --orange-text: #f7c9a8;
    --grey-dark: #474749;
    --grey-mid: #6a6a6c;
    --grey-logo: #58585a;
    --white: #ffffff;
    --paper: #f4f4f4;
    --backdrop: #2b2b2d;
  }
  * { box-sizing: border-box; margin: 0; padding: 0; }
  html, body {
    width: 1200px; height: 1200px; overflow: hidden;
    background: var(--backdrop);
    font-family: "Montserrat", sans-serif;
  }
  .sheet {
    width: 1200px; height: 1200px;
    display: flex; flex-direction: column; align-items: center; justify-content: center;
    gap: 50px;
  }
  .card {
    width: 880px; height: 503px; position: relative; overflow: hidden;
    box-shadow: 0 18px 40px rgba(0,0,0,.45);
  }

  /* Front */
  .card-front {
    background: linear-gradient(135deg, var(--white) 0%, var(--paper) 55%, #e6e6e6 100%);
    display: flex; align-items: center; justify-content: center;
  }
  .wordmark-front {
    display: flex; align-items: center; gap: 22px;
  }
  .wordmark-square {
    width: 44px; height: 44px; background: var(--orange);
  }
  .wordmark-front .wordmark-name {
    font-weight: 800; font-size: 66px; letter-spacing: 2px; color: var(--orange);
  }

  /* Back */
  .card-back {
    background: linear-gradient(160deg, var(--grey-dark) 0%, var(--grey-mid) 45%, var(--grey-dark) 100%);
    color: var(--white);
  }
  .wordmark-back {
    position: absolute; left: 56px; top: 58px;
    display: flex; align-items: center; gap: 14px;
  }
  .wordmark-back .wordmark-square { width: 26px; height: 26px; background: var(--white); }
  .wordmark-back .wordmark-name {
    font-weight: 800; font-size: 38px; letter-spacing: 1.5px; color: var(--white);
  }
  .divider {
    position: absolute; left: 56px; right: 200px; top: 170px;
    height: 2px; background: var(--orange);
  }
  .contact-list {
    position: absolute; left: 56px; top: 196px; list-style: none;
    font-weight: 300; font-size: 19px; line-height: 30px;
  }
  .contact-list li { display: flex; align-items: center; gap: 12px; }
  .contact-list svg { width: 16px; height: 16px; fill: none; stroke: var(--white); stroke-width: 1.6; }
  .person {
    position: absolute; right: 60px; top: 196px; text-align: right;
  }
  .person-name { font-weight: 700; font-size: 34px; }
  .person-title { font-weight: 300; font-size: 22px; margin-top: 2px; }
  .address {
    position: absolute; right: 60px; top: 296px; text-align: right;
    font-weight: 400; font-size: 19px; line-height: 28px;
  }
  .services-band {
    position: absolute; left: 0; right: 0; bottom: 0; height: 118px;
    background: linear-gradient(90deg, var(--orange-deep), var(--orange));
    display: flex; flex-direction: column; justify-content: center; align-items: center;
    color: var(--orange-text); font-weight: 400; font-size: 20px; line-height: 32px;
  }
</style>
</head>
<body>
<main class="sheet">
  <section class="card card-front" aria-label="Card front">
    <div class="wordmark-front">
      <span class="wordmark-square"></span>
      <span class="wordmark-name">FALCRIDGE HIRES</span>
    </div>
  </section>

  <section class="card card-back" aria-label="Card back">
    <div class="wordmark-back">
      <span class="wordmark-square"></span>
      <span class="wordmark-name">FALCRIDGE HIRES</span>
    </div>
    <div class="divider"></div>

    <ul class="contact-list">
      <li>
        <svg viewBox="0 0 16 16"><path d="M4 1.5l2.2 3-1.4 1.6c.8 1.9 2.2 3.3 4.1 4.1l1.6-1.4 3 2.2-1.2 2.5C7 13.2 2.8 9 1.5 3.2z"/></svg>
        555 318-0476
      </li>
      <li>
        <svg viewBox="0 0 16 16"><rect x="1.5" y="3.5" width="13" height="9"/><path d="M1.5 3.5l6.5 5 6.5-5"/></svg>
        info@falcridgehires.com
      </li>
      <li>
        <svg viewBox="0 0 16 16"><circle cx="8" cy="8" r="6.5"/><path d="M1.5 8h13M8 1.5c-3 3.5-3 9.5 0 13M8 1.5c3 3.5 3 9.5 0 13"/></svg>
        www.falcridgehires.com
      </li>
    </ul>

    <div class="person">
      <div class="person-name">Dwight Penner</div>
      <div class="person-title">CFO</div>
    </div>
    <address class="address" style="font-style:normal">
      4807 Alder Crest Road<br>
      Harbor Vale Maine 11584
    </address>

    <div class="services-band">
      <p>Luxury Restroom | Trailers Rental and Sales</p>
      <p>Weddings | Concerts | Charity | Sporting | Corp. Events</p>
    </div>
  </section>
</main>
</body>
</html>
```